Beacon Advisory Website

I currently have a website www.beaconadvisoryinc.com. We are a IT Consulting Company. Our website will pretty much tell out our services. I am looking to enhance my website and make it look more professional. Looking for very classy and Contemporary look and design for my website.

It Company

```html
<!DOCTYPE html>
<html lang="en">
<head>
<meta charset="utf-8">
<title>Beacon Advisory</title>
<link href="https://fonts.googleapis.com/css2?family=Lato:wght@400;700;900&family=Questrial&display=swap" rel="stylesheet">
<style>
:root{
  --blue:#0a68a8;
  --blue-dark:#07588f;
  --ink:#1a1a1a;
  --text:#333;
  --paper:#f7f7f7;
  --bar:#2b2b2b;
  --hero-top:#8e8a86;
  --hero-bottom:#d9d6d3;
}
*{margin:0;padding:0;box-sizing:border-box}
html,body{width:1015px;height:1200px;overflow:hidden}
body{position:relative;background:var(--paper);font-family:'Lato',sans-serif;color:var(--text)}
a{color:var(--blue);font-weight:700}
.abs{position:absolute}

.topbar{left:0;top:0;width:1015px;height:24px;background:linear-gradient(#555,#262626);color:#fff;font-size:12px}
.topbar .item{position:absolute;top:4px;display:flex;align-items:center;gap:7px}
.topbar .sep{position:absolute;left:717px;top:2px;width:1px;height:20px;background:#777}

.header{left:0;top:24px;width:1015px;height:70px;background:var(--paper)}
.brand{position:absolute;left:112px;top:20px;display:flex;align-items:center;gap:8px}
.brand .dot{width:30px;height:30px;border-radius:50%;background:var(--blue)}
.brand .name{font-family:'Lato',sans-serif;font-weight:900;font-size:18px;color:var(--blue);letter-spacing:.5px}
.nav{position:absolute;left:422px;top:0;height:70px;display:flex}
.nav a{display:flex;align-items:center;height:70px;padding:0 10px;font-size:13px;font-weight:700;color:var(--ink);text-decoration:none;border-right:1px solid #ddd}
.nav a:last-child{border-right:0}
.nav a.active{background:var(--blue);color:#fff;border-right:0}

.hero-bg{left:0;top:94px;width:1015px;height:452px;background:#cfcdcb}
.hero-photo{left:102px;top:94px;width:812px;height:452px;background:radial-gradient(ellipse at 50% 30%,#e4e2df 0%,#b8b4b0 55%,var(--hero-top) 100%)}
.hero-title{left:102px;top:356px;width:812px;text-align:center;font-family:'Questrial',sans-serif;font-size:26px;line-height:33px;color:#fff;text-shadow:0 2px 4px rgba(0,0,0,.55)}
.band{left:0;top:546px;width:1015px;height:183px;background:var(--blue)}

.card{position:absolute;top:438px;width:224px;height:258px;background:#fff;border:1px solid #cfcfcf;border-radius:10px 10px 0 10px;box-shadow:0 8px 8px -4px rgba(0,0,0,.45);text-align:center}
.card .photo{position:absolute;left:3px;top:3px;width:218px;height:116px;border-radius:8px 8px 0 0}
.card .badge{position:absolute;left:90px;top:108px;width:44px;height:30px;border-radius:50%;background:var(--blue);border:2px solid #fff}
.card h3{position:absolute;top:150px;width:100%;font-size:15px;font-weight:900;color:var(--ink);letter-spacing:.3px}
.card p{position:absolute;top:180px;left:14px;right:14px;font-size:10.5px;line-height:15.5px;color:#444}
.card a{position:absolute;top:234px;width:100%;left:0;font-size:11px}

.welcome-title{left:0;top:770px;width:1015px;text-align:center;font-size:27px;color:var(--ink)}
.welcome-title .lead{font-family:'Questrial',sans-serif}
.welcome-title .name{font-weight:900;color:var(--blue);letter-spacing:.5px}
.welcome-text{left:118px;top:814px;width:780px;text-align:center;font-size:13px;line-height:23px;color:#222}
.welcome-more{left:0;top:917px;width:1015px;text-align:center;font-size:11px}

.footer{left:0;top:978px;width:1015px;height:180px;background:var(--blue);color:#fff}
.news{left:120px;top:969px;width:242px;height:173px;background:#e4e4e4;clip-path:polygon(0 0,100% 0,100% 88%,88% 100%,0 100%)}
.news-fold{left:337px;top:1127px;width:0;height:0;border-left:15px solid transparent;border-bottom:15px solid #fff;opacity:.9}
.news h4{position:absolute;left:12px;top:22px;font-family:'Questrial',sans-serif;font-weight:400;font-size:14px;color:#333}
.news .arrows{position:absolute;right:18px;top:22px;font-size:13px;color:#555;letter-spacing:6px}
.news .rule{position:absolute;left:12px;right:12px;top:45px;height:1px;background:#bbb}
.news-item{position:absolute;left:12px;display:flex;gap:6px}
.date{width:39px;text-align:center;font-size:11px}
.date .m{background:var(--blue);color:#fff;height:15px;line-height:15px}
.date .d{background:#222;color:#fff;font-weight:700;font-size:14px;height:21px;line-height:21px}
.news-item p{font-size:11px;line-height:15px;color:#333;width:180px}

.col h5{font-family:'Questrial',sans-serif;font-weight:400;font-size:13px;letter-spacing:.3px;padding-bottom:4px;border-bottom:1px solid rgba(255,255,255,.6)}
.col ul{list-style:none;margin-top:10px}
.col li{font-size:11px;line-height:17.3px}
.vsep{top:994px;width:1px;height:140px;background:rgba(255,255,255,.25)}
.newsletter p{font-size:10.5px;line-height:15px;margin-top:11px}
.newsletter .field{margin-top:9px;width:175px;height:25px;background:#fff;border-radius:2px;color:#666;font-size:10px;padding:6px 10px}
.newsletter .btn{margin-top:10px;width:96px;height:25px;background:#fff;border-radius:3px;color:var(--blue);font-weight:900;font-size:11.5px;text-align:center;line-height:25px}
.contact .row{display:flex;gap:8px;font-size:11px;line-height:14.5px;margin-top:6px}
.contact .row svg{flex:none;margin-top:2px}

.bottombar{left:0;top:1158px;width:1015px;height:42px;background:#262626;color:#ddd;font-size:12.5px}
.bottombar .copy{position:absolute;left:112px;top:13px}
.social{position:absolute;right:111px;top:14px;display:flex;gap:17px}
.social span{width:14px;height:14px;border-radius:50%;background:#777;display:block}
</style>
</head>
<body>

<div class="abs topbar">
  <div class="item" style="left:582px">
    <svg width="11" height="13" viewBox="0 0 11 13"><path d="M2 1l2 2-1 2c1 2 2 3 4 4l1-1 2 2-1 2C5 12 0 7 1 2z" fill="#fff"/></svg>
    <span>+1 (555) 014 2290</span>
  </div>
  <div class="sep"></div>
  <div class="item" style="left:731px">
    <svg width="14" height="10" viewBox="0 0 14 10"><rect width="14" height="10" fill="#fff"/><path d="M0 0l7 5 7-5" stroke="#333" fill="none"/></svg>
    <span>info@beaconadvisoryinc.com</span>
  </div>
</div>

<header class="abs header">
  <div class="brand"><span class="dot"></span><span class="name">BEACON ADVISORY</span></div>
  <nav class="nav">
    <a class="active">HOME</a><a>SERVICES</a><a>SOLUTIONS</a><a>RESOURCES</a><a>CAREER</a><a>CONTACT US</a>
  </nav>
</header>

<div class="abs hero-bg"></div>
<div class="abs hero-photo" role="img" aria-label="Chess pieces: a blue king surrounded by white pawns"></div>
<h1 class="abs hero-title" style="font-weight:400">We Understand The Complexities Management<br>Faces When Staffing A Project.</h1>
<div class="abs band"></div>

<div class="card" style="left:112px">
  <div class="photo" role="img" aria-label="Business people reviewing a document on a tablet" style="background:linear-gradient(135deg,#d6dde6,#6d7d92)"></div>
  <div class="badge"></div>
  <h3>CONSULTING</h3>
  <p>Beacon Advisory has certified professional consultants to work with you to help increase the business ...</p>
  <a>Read More »</a>
</div>
<div class="card" style="left:395px">
  <div class="photo" role="img" aria-label="Silhouettes of a business team in a bright office" style="background:linear-gradient(180deg,#bfc6cc,#2b2b2b)"></div>
  <div class="badge"></div>
  <h3>STAFF AUGMENTATION</h3>
  <p>For years Beacon Advisory as been offering our customers the ability to augment their existing staff ...</p>
  <a>Read More »</a>
</div>
<div class="card" style="left:681px">
  <div class="photo" role="img" aria-label="Team analysing charts on paper at a desk" style="background:linear-gradient(135deg,#c8d3df,#eef1f4)"></div>
  <div class="badge"></div>
  <h3>OFFSHORE</h3>
  <p>Our Offshore development model has a unique distinction of providing efficient software solutions ...</p>
  <a>Read More »</a>
</div>

<h2 class="abs welcome-title" style="font-weight:400"><span class="lead">WELCOME TO </span><span class="name">BEACON ADVISORY</span></h2>
<p class="abs welcome-text">Today’s IT market is a dynamic, fast-paced industry, with ever-increasing demands. Meeting these demands for over 25 years, Beacon Advisory maintains a global presence, aggressively recruiting expertly qualified IT and Management Professionals from around the world and cultivating key partnerships with corporations to understand their business models end-to-end, with a goal of delivering exceptional client service and ensuring a consistent delivery of the talent needed to drive results.</p>
<div class="abs welcome-more"><a>Read More »</a></div>

<footer class="abs footer"></footer>
<div class="abs news">
  <h4>LATEST NEWS</h4>
  <span class="arrows">‹ ›</span>
  <div class="rule"></div>
  <div class="news-item" style="top:60px">
    <div class="date"><div class="m">MAR</div><div class="d">01</div></div>
    <p>Lorem ipsum dolor sit amet, Lorem consectetuer adipiscing elit, sed</p>
  </div>
  <div class="news-item" style="top:112px">
    <div class="date"><div class="m">MAR</div><div class="d">01</div></div>
    <p>Lorem ipsum dolor sit amet, Lorem consectetuer adipiscing elit, sed</p>
  </div>
</div>
<div class="abs news-fold"></div>

<div class="abs col" style="left:384px;top:995px;width:82px;color:#fff">
  <h5>QUICK LINKS</h5>
  <ul><li>› Home</li><li>› Services</li><li>› Solutions</li><li>› Resources</li><li>› Career</li><li>› Contact Us</li></ul>
</div>
<div class="abs vsep" style="left:486px"></div>
<div class="abs col newsletter" style="left:513px;top:995px;width:163px;color:#fff">
  <h5>NEWSLETTER</h5>
  <p>Get Latest Updates By Entering<br>Your Email Address</p>
  <div class="field">Email Address</div>
  <div class="btn">SUBSCRIBE</div>
</div>
<div class="abs vsep" style="left:708px"></div>
<div class="abs col contact" style="left:735px;top:995px;width:163px;color:#fff">
  <h5>CONTACT DETAILS</h5>
  <div class="row" style="margin-top:10px">
    <svg width="11" height="13" viewBox="0 0 11 13"><path d="M5.5 0a4.5 4.5 0 0 1 4.5 4.5c0 3-4.5 8.5-4.5 8.5S1 7.5 1 4.5A4.5 4.5 0 0 1 5.5 0z" fill="#fff"/><circle cx="5.5" cy="4.5" r="1.6" fill="#0a68a8"/></svg>
    <div><b>Beacon Advisory INC.</b><br>240 Harbor Lane<br>Suite 310<br>Eastfield, NJ 07000</div>
  </div>
  <div class="row">
    <svg width="11" height="12" viewBox="0 0 11 13"><path d="M2 1l2 2-1 2c1 2 2 3 4 4l1-1 2 2-1 2C5 12 0 7 1 2z" fill="#fff"/></svg>
    <div>+1 (555) 014 2290</div>
  </div>
  <div class="row">
    <svg width="11" height="10" viewBox="0 0 14 10"><rect width="14" height="10" fill="#fff"/><path d="M0 0l7 5 7-5" stroke="#0a68a8" fill="none"/></svg>
    <div>info@beaconadvisoryinc.com</div>
  </div>
</div>

<div class="abs bottombar">
  <span class="copy">© 2016 - Beacon Advisory INC. &nbsp;|&nbsp; All Rights Reserved</span>
  <div class="social" aria-label="Social links"><span></span><span></span><span></span><span></span></div>
</div>

</body>
</html>
```